Tidewell Health & Wellness Center Remedium

BluSketcho, Submit your previous card design as well as a couple others. Challenge yourself to make it great! You know what I want.
Updates

I would like to have a Chatterly logo beside my logo

Some designers are putting my information on the cards, but a lot are not using the information I have supplied. WHY?

I would to seed some designs on a BLACK background please, thank you.

Please include my titles "PharmD. RpH CuraLink" beside or under my name.

Industry/Entity Type

Health

Colors
add136

Requirements
Must have
• Tidewell Health & Wellness Center
Founder & President | Lou Pemberg
Gulfmere Florida, 34021
239-555-0187
Nice to have
• I would like to have a Chatterly logo and Tidewell Health & Wellness Remedium

```html
<!DOCTYPE html>
<html lang="en">
<head>
<meta charset="utf-8">
<title>Tidewell Health &amp; Wellness Center Remedium – Business Card</title>
<link href="https://fonts.googleapis.com/css2?family=Tinos:wght@400;700&display=swap" rel="stylesheet">
<style>
  :root {
    --backdrop: #5e5f60;
    --card-black: #0d0d0d;
    --card-black-edge: #1c1c1c;
    --brand-green: #6fae2c;
    --brand-lime: #add136;
    --green-deep: #3d8a35;
    --green-mid: #55a23a;
    --green-glow: #9fd25a;
    --text-light: #f2f4ee;
    --leaf-dark: #2f8a22;
    --leaf-light: #a6d84a;
  }
  * { margin: 0; padding: 0; box-sizing: border-box; }
  html, body { width: 1200px; height: 1200px; overflow: hidden; }
  body {
    background: var(--backdrop);
    font-family: "Tinos", "Times New Roman", serif;
    position: relative;
  }
  .card {
    position: absolute;
    left: 150px;
    width: 900px;
    height: 514px;
    overflow: hidden;
    box-shadow: 0 10px 30px rgba(0,0,0,0.45);
  }

  /* Back side */
  .card--back {
    top: 60px;
    background: radial-gradient(ellipse at 55% 45%, var(--card-black-edge), var(--card-black) 70%);
  }
  .leaf-cluster {
    position: absolute;
    border-radius: 50%;
    background: radial-gradient(circle, var(--leaf-light) 0%, var(--leaf-dark) 60%, rgba(47,138,34,0) 72%);
  }
  .leaf-cluster--top-left { left: 60px; top: -70px; width: 220px; height: 170px; }
  .leaf-cluster--bottom-left { left: -70px; top: 250px; width: 220px; height: 170px; }
  .leaf-cluster--top-right { right: -60px; top: 90px; width: 200px; height: 160px; }
  .leaf-cluster--bottom-right { right: -40px; bottom: -50px; width: 260px; height: 210px; }

  .brand-circle {
    position: absolute;
    left: 410px;
    top: 60px;
    width: 220px;
    height: 220px;
    border-radius: 50%;
    background: radial-gradient(circle at 40% 35%, #ffffff, #dfeedd 60%, #b9d9a8);
    box-shadow: 0 0 0 10px rgba(120,190,70,0.35);
  }
  .brand-glow {
    position: absolute;
    left: 390px;
    top: 300px;
    width: 260px;
    height: 22px;
    border-radius: 50%;
    background: radial-gradient(ellipse, rgba(140,200,80,0.55), rgba(140,200,80,0) 70%);
  }
  .back-wordmark {
    position: absolute;
    left: 0;
    right: 0;
    top: 312px;
    text-align: center;
    color: var(--brand-green);
  }
  .back-wordmark__name {
    font-size: 104px;
    line-height: 1;
    letter-spacing: 1px;
  }
  .back-wordmark__tagline {
    font-size: 30px;
    margin-top: 6px;
  }

  /* Front side */
  .card--front {
    top: 626px;
    background: radial-gradient(ellipse at 52% 40%, var(--green-glow) 0%, var(--green-mid) 38%, var(--green-deep) 100%);
    color: var(--text-light);
  }
  .front-header {
    position: absolute;
    left: 0;
    right: 0;
    top: 28px;
    text-align: center;
  }
  .front-header__name { font-size: 96px; line-height: 1; }
  .front-header__tagline { font-size: 28px; margin-top: 4px; }

  .contact-divider {
    position: absolute;
    left: 470px;
    top: 212px;
    width: 3px;
    height: 170px;
    background: var(--text-light);
  }
  .person {
    position: absolute;
    right: 450px;
    top: 200px;
    text-align: right;
  }
  .person__name { font-size: 56px; line-height: 1.05; letter-spacing: 1px; }
  .person__role { font-size: 30px; line-height: 1.25; }
  .person__titles { font-size: 30px; line-height: 1.25; }

  .contact {
    position: absolute;
    left: 496px;
    top: 214px;
    font-size: 32px;
    line-height: 1.2;
  }
  .contact__email { font-size: 27px; margin-top: 4px; }

  .social {
    position: absolute;
    left: 0;
    right: 0;
    top: 420px;
    display: flex;
    justify-content: center;
    align-items: center;
    gap: 16px;
    font-size: 38px;
  }
  .social__square {
    width: 40px;
    height: 40px;
    background: var(--text-light);
  }
</style>
</head>
<body>

  <section class="card card--back" aria-label="Card back">
    <div class="leaf-cluster leaf-cluster--top-left" role="img" aria-label="Cluster of green leaf illustrations"></div>
    <div class="leaf-cluster leaf-cluster--bottom-left" role="img" aria-label="Cluster of green leaf illustrations"></div>
    <div class="leaf-cluster leaf-cluster--top-right" role="img" aria-label="Cluster of green leaf illustrations"></div>
    <div class="leaf-cluster leaf-cluster--bottom-right" role="img" aria-label="Cluster of green leaf illustrations"></div>

    <div class="brand-circle"></div>
    <div class="brand-glow"></div>

    <div class="back-wordmark">
      <div class="back-wordmark__name">Tidewell</div>
      <div class="back-wordmark__tagline">Health &amp; Wellness Center Remedium</div>
    </div>
  </section>

  <section class="card card--front" aria-label="Card front">
    <header class="front-header">
      <div class="front-header__name">Tidewell</div>
      <div class="front-header__tagline">Health &amp; Wellness Center Remedium</div>
    </header>

    <div class="person">
      <div class="person__name">LOU PEMBERG</div>
      <div class="person__role">President &amp; Founder</div>
      <div class="person__titles">PharmD., R.Ph, CuraLink</div>
    </div>

    <div class="contact-divider"></div>

    <div class="contact">
      <div class="contact__phone">239-555-0187</div>
      <div class="contact__city">Gulfmere</div>
      <div class="contact__state">Florida, 34021</div>
      <div class="contact__email">loupemberg01@postwren.com</div>
    </div>

    <div class="social">
      <span class="social__square"></span>
      <span class="social__network">Chatterly</span>
      <span class="social__page">Tidewell Health &amp; Wellness</span>
    </div>
  </section>

</body>
</html>
```